Lantern Petals Website v.1 - attract floral shop franchisees

I need a simple information website for my new business. We are a franchisor of flower shops. The overall purpose of the website is to promote the company and the service, especially to potential franchisees and retailers. Only about 4 pages are required including homepage, About, For Supermarkets, For Franchisees, and Contact. No special functions are required except the site will have two separate inquiry forms that must be filled out online and submitted via automated email. Similarly, an email form should be linked from the Contact page. I have a logo and business cards designed by ArtMingle, and I would like the site to have a consistent color scheme and style. The key to design will be to express the joy and love associated with flowers and floral bouquets.
IMPORTANT - I will be exporting the website design to Wordpress CMS in a site hosted by HostNimbus. For smooth integration into WordPress hosted by HostNimbus, the designer should build the site using a WordPress-friendly format. Ideally, they should use HTML, CSS, and PHP. Creating a custom theme or using a page builder that exports to WordPress-compatible files is best. This ensures the site can be easily imported and managed within WordPress.

Target Market(s)

Potential franchisees (existing florists or creative types who might like to own a floral business) and supermarkets who might want us to run their floral department

Industry/Entity Type

Floral retailing

Requirements
Must have
• A brand theme that is beautiful, consistent throughout and builds on the logo design
Nice to have
• Show gender and ethnic diversity in customers and florists. Pictures of happy florists (for franchisees) and pictures of amazing floral department displays (for supermarkets)

```html
<!DOCTYPE html>
<html lang="en">
<head>
<meta charset="utf-8">
<title>Lantern Petals</title>
<link href="https://fonts.googleapis.com/css2?family=Roboto:wght@400;500;700&family=Yellowtail&display=swap" rel="stylesheet">
<style>
:root{
  --green:#008c44;
  --green-dark:#0a5a2c;
  --orange:#f0a020;
  --ink:#333333;
  --dark:#262626;
  --light:#f2f2f0;
  --white:#ffffff;
}
*{box-sizing:border-box;margin:0;padding:0}
html,body{width:1200px;height:3543px;overflow:hidden}
body{font-family:'Roboto',sans-serif;color:var(--ink);background:var(--white);position:relative}
.abs{position:absolute}
.script{font-family:'Yellowtail',cursive;font-weight:400;line-height:1}
.rule{display:block;width:46px;height:4px;background:var(--orange);border-radius:2px;margin-top:10px}
p.body{font-size:16px;line-height:26px;text-align:justify}
.btn{position:absolute;display:flex;align-items:center;justify-content:center;border-radius:30px;font-size:15px;font-weight:500;text-transform:uppercase;letter-spacing:.2px;z-index:3}
.btn-solid{background:var(--orange);color:var(--white)}
.btn-line{border:2px solid var(--orange);color:var(--green)}
.btn-line-light{border:2px solid var(--orange);color:var(--white)}
.soc{width:34px;height:34px;border-radius:50%;display:flex;align-items:center;justify-content:center;font-size:13px;font-weight:700}

/* top bar */
.topbar{left:0;top:0;width:1200px;height:117px;background:var(--green)}
.topbar .info{left:111px;top:17px;color:var(--white);font-size:16px;display:flex;gap:30px;align-items:center}
.topbar .info svg{margin-right:10px;vertical-align:-2px}
.socials{display:flex;gap:6px}
.socials .soc{border:2px solid var(--orange);color:var(--white)}
.socials .soc.fill{background:var(--orange)}
.topbar .socials{left:976px;top:12px}

.navbar{left:77px;top:54px;width:1046px;height:104px;background:var(--white);border-radius:52px;box-shadow:0 6px 18px rgba(0,0,0,.18);z-index:10}
.brand{left:36px;top:34px;display:flex;align-items:center;gap:10px;color:var(--orange);font-size:24px;font-weight:500}
.brand .dot{width:34px;height:34px;border-radius:50%;border:2px solid var(--green)}
.menu{right:34px;top:43px;display:flex;gap:46px;font-size:15px;font-weight:500;color:#111}
.menu .active{color:var(--orange)}

/* hero */
.hero{left:0;top:117px;width:1200px;height:708px;
  background:
   radial-gradient(ellipse 320px 260px at 930px 330px,rgba(232,92,52,.85),rgba(232,92,52,0) 70%),
   radial-gradient(ellipse 260px 220px at 160px 520px,rgba(176,42,36,.75),rgba(176,42,36,0) 70%),
   radial-gradient(ellipse 300px 240px at 420px 420px,rgba(190,206,160,.55),rgba(190,206,160,0) 70%),
   linear-gradient(100deg,#3f5236 0%,#6d7a62 40%,#8f9580 58%,#587548 80%,#3c5e33 100%)}
.hero-title{left:111px;top:300px;color:var(--white);font-size:60px;z-index:2}
.hero-text{left:111px;top:380px;width:430px;color:var(--white);font-size:20px;line-height:29px;font-weight:500;z-index:2}
.hero-wave{left:0;top:640px;z-index:1}

/* about */
.about-ring{left:92px;top:855px;width:504px;height:504px;border-radius:50%;background:var(--green)}
.about-photo{left:112px;top:870px;width:474px;height:474px;border-radius:50%;background:linear-gradient(160deg,#f4efe8 0%,#e6cfb0 40%,#c99a6e 60%,#efe6dc 100%)}
.about-badge{left:408px;top:1168px;width:188px;height:188px;border-radius:50%;background:var(--white);box-shadow:0 6px 18px rgba(0,0,0,.2);display:flex;align-items:center;justify-content:center}
.about-badge span{width:150px;height:150px;border-radius:50%;border:2px solid var(--orange)}
.about-copy{left:649px;top:880px;width:440px}
.about-copy h2,.fr-copy h2{color:var(--green);font-size:50px}
.about-copy p{margin-top:16px}

/* supermarkets */
.market{left:0;top:1479px;width:1200px;height:515px;
  background:
   radial-gradient(ellipse 200px 180px at 760px 270px,rgba(250,248,240,.95),rgba(250,248,240,0) 75%),
   linear-gradient(90deg,#0c7a36 0%,#118a3e 45%,#4f8a55 56%,#dcdcd4 70%,#2f3d5e 82%,#e8e6e1 92%,#b8b2aa 100%)}
.market-copy{left:113px;top:1555px;width:440px;color:var(--white)}
.market-copy h2{font-size:50px}
.market-copy p{margin-top:24px}

/* franchisees */
.fr-orange{left:212px;top:2365px;width:200px;height:200px;border-radius:50%;background:var(--orange)}
.fr-a{left:111px;top:2121px;width:300px;height:300px;border-radius:50%;background:linear-gradient(135deg,#7fa07a 0%,#d9b99a 45%,#e6dccf 70%,#a8876a 100%)}
.fr-b{left:377px;top:2182px;width:150px;height:150px;border-radius:50%;border:6px solid var(--white);background:linear-gradient(135deg,#f4f3ef,#c9cdd0 60%,#8e969c)}
.fr-c{left:312px;top:2295px;width:284px;height:284px;border-radius:50%;border:6px solid var(--white);background:linear-gradient(135deg,#fbe9dd 0%,#f2a9a6 45%,#fbf4ee 75%,#e8d6cf 100%)}
.fr-copy{left:649px;top:2142px;width:440px}
.fr-copy p{margin-top:16px}

/* get started */
.start{left:0;top:2695px;width:1200px;height:520px;background:var(--light)}
.start-photo{left:30px;top:2705px;width:500px;height:500px;border-radius:48% 48% 40% 40%;
  background:
   radial-gradient(circle at 40% 40%,#d679b0 0%,rgba(214,121,176,0) 28%),
   radial-gradient(circle at 68% 55%,#f3a0a0 0%,rgba(243,160,160,0) 25%),
   radial-gradient(circle at 25% 60%,#8a6fc2 0%,rgba(138,111,194,0) 22%),
   linear-gradient(180deg,#9dbb86 0%,#7fa36e 55%,#c9d48a 100%)}
.start-copy{left:580px;top:2765px;width:500px}
.start-copy h2{color:var(--green);font-size:50px}
.start-copy p{margin-top:18px;font-size:16px;line-height:24px}

/* footer */
.footer{left:0;top:3080px;width:1200px;height:463px}
.foot-brand{left:111px;top:3350px;color:var(--white);font-size:28px;font-weight:500;display:flex;align-items:center;gap:12px}
.foot-brand .dot{width:46px;height:46px;border-radius:50%;border:2px solid var(--white)}
.foot-h{color:var(--white);font-size:18px;font-weight:500;text-transform:uppercase}
.foot-nav{left:392px;top:3238px}
.foot-nav ul{list-style:none;margin-top:18px}
.foot-nav li{color:var(--white);font-size:15px;height:37px;display:flex;align-items:center;gap:18px}
.foot-loc{left:606px;top:3238px}
.map{left:606px;top:3282px;width:222px;height:142px;border:4px solid var(--green);background:linear-gradient(135deg,#e3e6e4,#cfd4d2)}
.foot-contact{left:895px;top:3238px;width:240px;color:var(--white)}
.foot-contact .item{display:flex;gap:20px;margin-top:18px}
.foot-contact b{display:block;font-size:15px;font-weight:500;text-transform:uppercase}
.foot-contact small{display:block;font-size:12px;line-height:19px;margin-top:4px}
.foot-line{left:111px;top:3475px;width:978px;height:1px;background:#4a4a4a}
.copy{left:0;top:3494px;width:1200px;text-align:center;color:var(--white);font-size:13px}
.foot-socials{left:976px;top:3486px}
</style>
</head>
<body>

<div class="abs topbar">
  <div class="abs info">
    <span><svg width="14" height="14" viewBox="0 0 24 24"><path fill="#f0a020" d="M6.6 10.8a15 15 0 0 0 6.6 6.6l2.2-2.2a1 1 0 0 1 1-.25 11.4 11.4 0 0 0 3.6.57 1 1 0 0 1 1 1V20a1 1 0 0 1-1 1A17 17 0 0 1 3 4a1 1 0 0 1 1-1h3.5a1 1 0 0 1 1 1c0 1.25.2 2.45.57 3.57a1 1 0 0 1-.25 1z"/></svg>+1.555.204.7781</span>
    <span>|</span>
    <span><svg width="15" height="12" viewBox="0 0 24 18"><path fill="#f0a020" d="M0 0h24v2L12 9 0 2zM0 4l12 7 12-7v14H0z"/></svg>info@Lantern-Petals.com</span>
  </div>
  <div class="abs socials"><span class="soc fill">f</span><span class="soc">ig</span><span class="soc">in</span></div>
</div>

<section class="abs hero" role="img" aria-label="Flower shop interior with a colourful bouquet of red and orange roses in the foreground"></section>

<nav class="abs navbar">
  <div class="abs brand"><span class="dot"></span>Lantern Petals</div>
  <div class="abs menu"><span class="active">HOME</span><span>ABOUT US</span><span>FOR SUPERMARKETS</span><span>FOR FRANCHISEES</span><span>CONTACT</span></div>
</nav>

<h1 class="abs script hero-title">Lantern Petals</h1>
<p class="abs hero-text">Fresh flowers convey beauty and love, and in our view should become something every person regularly enjoys.</p>
<a class="btn btn-solid" style="left:111px;top:490px;width:141px;height:45px">Contact Us</a>
<svg class="abs hero-wave" width="1200" height="190" viewBox="0 0 1200 190">
  <path fill="#f0a020" d="M560 120 C760 180 1000 190 1200 60 L1200 190 L560 190Z"/>
  <path fill="#ffffff" d="M0 170 C120 70 250 30 360 45 C520 70 650 175 860 180 C1000 183 1120 140 1200 95 L1200 190 L0 190Z"/>
</svg>

<div class="abs about-ring"></div>
<div class="abs about-photo" role="img" aria-label="Hand holding a dried flower bouquet"></div>
<div class="abs about-badge"><span></span></div>
<div class="abs about-copy">
  <h2 class="script">About Us</h2><span class="rule"></span>
  <p class="body" style="margin-top:34px">Fresh flowers convey beauty and love, and in our view should become something every person regularly enjoys. Lantern Petals is an entrepreneurial company created to make top quality fresh flowers and professionally-designed bouquets accessible to every consumer at affordable prices.</p>
  <p class="body">Professional florists typically sell the finest quality stems, design the most beautiful bouquets and provide the finest customer service, but their costs – of floral products, retail spaces, labor and marketing – force them to pass high prices along to customers.</p>
</div>
<a class="btn btn-line" style="left:649px;top:1281px;width:144px;height:47px">Learn More</a>

<section class="abs market" role="img" aria-label="Bride and groom holding a bouquet of white roses"></section>
<div class="abs market-copy">
  <h2 class="script">For Supermarkets</h2><span class="rule"></span>
  <p class="body">Lantern Petals works with some of the country's largest and most progressive supermarkets to provide franchisee ownership and operation of their strategically important floral departments. Supermarkets find that Lantern Petals is able to improve their financial outcomes, provide attentive customer service and satisfaction, and lift the quality of the entire store environment.</p>
</div>
<a class="btn btn-line-light" style="left:113px;top:1864px;width:144px;height:47px">Learn More</a>

<div class="abs fr-orange"></div>
<div class="abs fr-a" role="img" aria-label="Two florists working at a laptop in a flower shop"></div>
<div class="abs fr-b" role="img" aria-label="White bouquet held by a bride"></div>
<div class="abs fr-c" role="img" aria-label="Pink and white roses with hydrangeas"></div>
<div class="abs fr-copy">
  <h2 class="script">For Franchisees</h2><span class="rule"></span>
  <p class="body" style="margin-top:34px">Lantern Petals brings the best of professional florists and supermarkets together for the benefit of consumers. It supports a national network of owner-operator franchisees, who in many cases are multi-site professional florists, with comprehensive services to enhance franchise profitability. Lantern Petals works with some of the country's largest and most progressive supermarkets to provide franchisee ownership and operation of their strategically important floral departments.</p>
</div>
<a class="btn btn-line" style="left:649px;top:2502px;width:144px;height:47px">Learn More</a>

<section class="abs start"></section>
<div class="abs start-photo" role="img" aria-label="Mixed spring bouquet with peonies, lilac and eucalyptus"></div>
<div class="abs start-copy">
  <h2 class="script">Get Started</h2><span class="rule"></span>
  <p>Sed ut perspiciatis unde omnis iste natus error sit voluptatem accu santium doloremque laudantiea.</p>
</div>
<a class="btn btn-solid" style="left:580px;top:2915px;width:286px;height:46px">New Florist Franchise Inquiry</a>
<a class="btn btn-line" style="left:580px;top:2974px;width:363px;height:46px">Professional Florist Franchise Inquiry</a>

<svg class="abs footer" width="1200" height="463" viewBox="0 0 1200 463">
  <path fill="#f0a020" d="M0 110 C200 150 420 80 700 20 C900 -20 1100 40 1200 110 L1200 463 L0 463Z"/>
  <path fill="#262626" d="M0 140 C220 175 440 100 720 45 C900 10 1080 80 1200 180 L1200 463 L0 463Z"/>
</svg>
<div class="abs foot-brand"><span class="dot"></span>Lantern Petals</div>
<div class="abs foot-nav">
  <div class="foot-h">Navigation</div>
  <ul>
    <li><svg width="14" height="14" viewBox="0 0 14 14"><circle cx="7" cy="7" r="7" fill="#008c44"/><path d="M4 7h6M7.5 4.5 10 7l-2.5 2.5" stroke="#262626" stroke-width="1.6" fill="none"/></svg>Home</li>
    <li><svg width="14" height="14" viewBox="0 0 14 14"><circle cx="7" cy="7" r="7" fill="#008c44"/><path d="M4 7h6M7.5 4.5 10 7l-2.5 2.5" stroke="#262626" stroke-width="1.6" fill="none"/></svg>About Us</li>
    <li><svg width="14" height="14" viewBox="0 0 14 14"><circle cx="7" cy="7" r="7" fill="#008c44"/><path d="M4 7h6M7.5 4.5 10 7l-2.5 2.5" stroke="#262626" stroke-width="1.6" fill="none"/></svg>For Supermarkets</li>
    <li><svg width="14" height="14" viewBox="0 0 14 14"><circle cx="7" cy="7" r="7" fill="#008c44"/><path d="M4 7h6M7.5 4.5 10 7l-2.5 2.5" stroke="#262626" stroke-width="1.6" fill="none"/></svg>For Franchisees</li>
    <li><svg width="14" height="14" viewBox="0 0 14 14"><circle cx="7" cy="7" r="7" fill="#008c44"/><path d="M4 7h6M7.5 4.5 10 7l-2.5 2.5" stroke="#262626" stroke-width="1.6" fill="none"/></svg>Contact</li>
  </ul>
</div>
<div class="abs foot-loc foot-h">Location</div>
<div class="abs map" role="img" aria-label="Location map"></div>
<div class="abs foot-contact">
  <div class="foot-h">Contact Info</div>
  <div class="item"><svg width="12" height="16" viewBox="0 0 12 16"><path fill="#008c44" d="M6 0a6 6 0 0 1 6 6c0 4-6 10-6 10S0 10 0 6a6 6 0 0 1 6-6zm0 3.5a2.5 2.5 0 1 0 0 5 2.5 2.5 0 0 0 0-5z"/></svg><div><b>Address:</b><small>465, Lorum Ipsum Dolore Sed,<br>United States</small></div></div>
  <div class="item"><svg width="14" height="14" viewBox="0 0 24 24"><path fill="#008c44" d="M6.6 10.8a15 15 0 0 0 6.6 6.6l2.2-2.2a1 1 0 0 1 1-.25 11.4 11.4 0 0 0 3.6.57 1 1 0 0 1 1 1V20a1 1 0 0 1-1 1A17 17 0 0 1 3 4a1 1 0 0 1 1-1h3.5a1 1 0 0 1 1 1c0 1.25.2 2.45.57 3.57a1 1 0 0 1-.25 1z"/></svg><div><b>Phone:</b><small>+1.555.204.7781</small></div></div>
  <div class="item"><svg width="15" height="12" viewBox="0 0 24 18"><path fill="#008c44" d="M0 0h24v2L12 9 0 2zM0 4l12 7 12-7v14H0z"/></svg><div><b>Email:</b><small>info@Lantern-Petals.com</small></div></div>
</div>
<div class="abs foot-line"></div>
<div class="abs copy">© 2024 <b>LANTERN PETALS</b> &nbsp;| &nbsp;All Rights Reserved</div>
<div class="abs socials foot-socials"><span class="soc fill" style="color:#fff">f</span><span class="soc">ig</span><span class="soc">in</span></div>

</body>
</html>
```